Velk Partners Building Business Cards

We need a business card that reflects our business as "Solar Experts" in San Diego. Browse our website www.velkpartners.example our License needs to be displayed as "CSLB# 3867140" our phone number is (619) 555-0187

Save thousands on your electric bills and increase the value of your home while helping to protect the environment. Our solar installation experts will help you design the system that's right for you, using only the highest quality equipment that will look great and give you ideal performance. Our goal is to make you energy independent, and get your electric bill to 0.

Paul Osterby
(619) 555-0187
paul@velkpartners.example

Target Market(s)

Home owners in san diego looking for solar

Industry/Entity Type

Solar Energy

Contact Information for Business Card

Paul Osterby
(619) 555-0187
paul@velkpartners.example

Font styles to use
Other font styles liked:
• Use our logo font

Requirements
Must have
• License needs to be displayed as "CSLB# 3867140" our phone number is (619) 555-0187
Nice to have
• Real images of rooftop home solar in san diego
Should not have
• our business address

```html
<!DOCTYPE html>
<html lang="en">
<head>
<meta charset="utf-8">
<title>Velk Partners Building — Business Cards</title>
<link rel="stylesheet" href="https://fonts.googleapis.com/css2?family=Source+Sans+3:ital,wght@0,400;0,600;0,700;1,400&display=swap">
<style>
  :root {
    --navy: #1b3c78;
    --gold: #f6ab00;
    --white: #ffffff;
    --backdrop: #4d4d4d;
    --card-radius: 20px;
  }
  * { box-sizing: border-box; margin: 0; padding: 0; }
  html, body {
    width: 1105px;
    height: 1200px;
    overflow: hidden;
    background: var(--backdrop);
    font-family: "Source Sans 3", Arial, sans-serif;
  }
  .canvas { position: relative; width: 1105px; height: 1200px; }
  .card {
    position: absolute;
    left: 193px;
    width: 719px;
    height: 411px;
    border-radius: var(--card-radius);
    overflow: hidden;
  }
  .card--front { top: 167px; background: var(--white); }
  .card--back { top: 624px; background: var(--navy); }

  .brand-name {
    position: absolute;
    font-weight: 700;
    letter-spacing: -0.5px;
    white-space: nowrap;
    display: flex;
    align-items: center;
    gap: 12px;
  }
  .brand-name .brand-dot {
    width: 20px; height: 20px; border-radius: 50%;
    background: var(--gold);
    flex: none;
  }
  .card--front .brand-name { left: 44px; top: 50px; font-size: 40px; color: var(--navy); }
  .card--back .brand-name {
    left: 0; right: 0; top: 170px; justify-content: center;
    font-size: 50px; color: var(--white);
  }

  .sun-disc { position: absolute; left: 0; top: 0; }

  .holder { position: absolute; left: 44px; top: 256px; }
  .holder-name { font-size: 27px; font-weight: 600; color: var(--navy); line-height: 1.1; }
  .holder-title { font-size: 19px; color: var(--gold); margin-top: 4px; }

  .contact {
    position: absolute;
    right: 29px;
    top: 192px;
    list-style: none;
    text-align: right;
    color: var(--white);
    font-size: 19px;
    line-height: 1;
  }
  .contact li {
    display: flex; justify-content: flex-end; align-items: center;
    gap: 9px; height: 27px;
  }
  .contact .license { margin-bottom: 8px; padding-right: 0; }
  .contact .icon { width: 16px; height: 16px; flex: none; }

  .back-url {
    position: absolute; left: 0; right: 0; top: 338px;
    text-align: center;
    color: var(--white);
    font-size: 20px;
    font-style: italic;
    letter-spacing: 6px;
  }
</style>
</head>
<body>
<div class="canvas">

  <section class="card card--front">
    <svg class="sun-disc" width="719" height="411" viewBox="0 0 719 411" role="img" aria-label="Large gold sun decoration">
      <circle cx="622" cy="378" r="214" fill="var(--gold)"/>
    </svg>

    <div class="brand-name"><span class="brand-dot"></span>Velk Partners Building</div>

    <div class="holder">
      <p class="holder-name">Paul Osterby</p>
      <p class="holder-title">CEO/Founder</p>
    </div>

    <ul class="contact">
      <li class="license">CSLB# 3867140</li>
      <li>(619) 555-0187
        <svg class="icon" viewBox="0 0 16 16" aria-hidden="true"><path fill="#fff" d="M3.5 1.2l2.4 2.6-1.2 1.9c.8 2 2.6 3.8 4.6 4.6l1.9-1.2 2.6 2.4-1.2 2.6C7.7 14 2 8.3 1 3.5z"/></svg>
      </li>
      <li>paul@velkpartners.example
        <svg class="icon" viewBox="0 0 16 16" aria-hidden="true"><rect x="1" y="3" width="14" height="10" fill="#fff"/><path d="M1 3l7 6 7-6" fill="none" stroke="var(--gold)" stroke-width="1.3"/></svg>
      </li>
      <li>www.velkpartners.example
        <svg class="icon" viewBox="0 0 16 16" aria-hidden="true"><circle cx="8" cy="8" r="7" fill="#fff"/><path d="M5 4c2 1 1 3 3 3s1 3-1 4M10 3c-1 2 2 2 3 4" fill="none" stroke="var(--gold)" stroke-width="1.3"/></svg>
      </li>
    </ul>
  </section>

  <section class="card card--back">
    <div class="brand-name"><span class="brand-dot"></span>Velk Partners Building</div>
    <p class="back-url">www.velkpartners.example</p>
  </section>

</div>
</body>
</html>
```